Flyer Design for Private Car Service

Flyer should cater to Business Travelers and Executives who travel Business Class or First Class.
Flyer should include images attached.
Flyer should include the below text
Dallas to Austin
Chauffeured SUVs
• Travel Dallas to Austin in a new 2025 Norvak Tressel for $499 one-way
• Trip includes a Uniformed Chauffeur who has a Commercial Drivers License (CDL)
• You can Schedule Chauffeur Pickup at Your Home in Dallas
• Our Chauffeur will Drop You Off at Your Final Destination in Austin
• You can Schedule Chauffeur Return Pickup in Austin and Return Back to Dallas.
• We offer Faster Times on Door-to-Door Travel than Bluequill Airways
• We offer Comparable Prices on Door-to-Door Travel Times than Bluequill Airways
• All of our trips are insured with $500k of commercial auto insurance
• Our Passengers can Talk on Cell Phone & Conduct Kavlo calls Throughout Travel
• Our Passengers have Maximum Privacy, Comfort and First-Class Amenities.
• Our Passengers Avoid Marrow Pike Airfield and QHN Airport hassles & delays
• Member Tellbrook Chamber of Commerce, Pindle Chamber of Commerce.
• Book your trip today at www.quorvanride.example
Target Market(s)
Business Travelers
Look and feel

```html
<!DOCTYPE html>
<html lang="en">
<head>
<meta charset="utf-8">
<title>Dallas to Austin Chauffeured SUVs Flyer</title>
<link href="https://fonts.googleapis.com/css2?family=Poppins:wght@400;500;700&family=Saira+Condensed:wght@700;800&display=swap" rel="stylesheet">
<style>
  :root{
    --red:#e8223c;
    --black:#0b0b0b;
    --white:#ffffff;
    --ink:#1c1c1c;
    --grey:#555a5e;
    --backdrop:#e9ecee;
    --photo-dark:#2b2b2e;
    --photo-light:#b9bcc0;
  }
  *{margin:0;padding:0;box-sizing:border-box}
  html,body{width:1200px;height:1200px;overflow:hidden;background:var(--backdrop)}
  .stage{position:relative;width:1200px;height:1200px;display:flex;justify-content:center;align-items:center}
  .flyer-frame{width:856px;height:1200px;position:relative;overflow:hidden}
  .flyer{position:absolute;left:0;top:0;width:1130px;height:1585px;background:var(--white);
    transform:scale(0.7571);transform-origin:0 0;font-family:"Poppins",sans-serif;color:var(--ink)}
  .flyer-shapes{position:absolute;inset:0;width:1130px;height:1585px}
  .brand{position:absolute;left:0;width:560px;top:120px;text-align:center;display:flex;justify-content:center;align-items:center;gap:14px}
  .brand-dot{width:22px;height:22px;border-radius:50%;background:var(--red)}
  .brand-name{font-family:"Poppins",sans-serif;font-weight:500;font-size:50px;letter-spacing:3px;color:var(--ink);text-transform:uppercase}
  .headline{position:absolute;left:70px;top:280px;font-family:"Saira Condensed",sans-serif;font-weight:800;
    font-size:84px;line-height:77px;color:var(--white);text-transform:uppercase;transform:skewX(-9deg);letter-spacing:1px}
  .intro{position:absolute;left:67px;top:622px;font-size:28px;line-height:36px;color:var(--grey);letter-spacing:.3px}
  .price{position:absolute;left:68px;top:712px;height:143px;display:flex;align-items:center;color:var(--white)}
  .price-currency{font-family:"Saira Condensed",sans-serif;font-weight:700;font-size:70px;color:var(--red);align-self:flex-start;margin-top:22px}
  .price-amount{font-family:"Saira Condensed",sans-serif;font-weight:700;font-size:138px;line-height:1;margin-right:24px}
  .price-term{font-size:56px;line-height:52px;font-weight:400}
  .benefits{position:absolute;list-style:none;font-size:24px;line-height:29px;color:var(--ink)}
  .benefits li{position:relative;padding-left:40px}
  .benefits li::before{content:"";position:absolute;left:0;top:3px;width:24px;height:24px;border-radius:50%;background:var(--red)}
  .benefits li::after{content:"";position:absolute;left:7px;top:9px;width:10px;height:6px;border-left:3px solid var(--white);border-bottom:3px solid var(--white);transform:rotate(-45deg)}
  .benefits-left{left:68px;top:891px}
  .benefits-left li{margin-bottom:33px}
  .benefits-left li:nth-child(2){margin-bottom:25px}
  .benefits-right{left:588px;top:893px}
  .benefits-right li{margin-bottom:28px}
  .cta{position:absolute;left:0;width:570px;top:1425px;text-align:center;color:var(--white)}
  .cta-lead{font-weight:700;font-size:34px;line-height:70px;padding-right:40px}
  .cta-url{font-size:38px;line-height:70px;padding-right:40px}
</style>
</head>
<body>
<div class="stage">
  <div class="flyer-frame">
    <div class="flyer">
      <svg class="flyer-shapes" viewBox="0 0 1130 1585" xmlns="http://www.w3.org/2000/svg">
        <defs>
          <linearGradient id="photoTop" x1="0" y1="0" x2="1" y2="1">
            <stop offset="0" stop-color="#c9ccd0"/>
            <stop offset=".45" stop-color="#3a3a3e"/>
            <stop offset="1" stop-color="#8d8f93"/>
          </linearGradient>
          <linearGradient id="photoBottom" x1="0" y1="0" x2="0" y2="1">
            <stop offset="0" stop-color="#b7bbc0"/>
            <stop offset=".5" stop-color="#2e2e31"/>
            <stop offset="1" stop-color="#1a1a1c"/>
          </linearGradient>
        </defs>
        <polygon points="500,258 590,0 605,0 515,258" fill="var(--black)"/>
        <path d="M600 0 H1130 V458 L1082 588 Q1073 610 1048 610 H548 L560 560 Z" fill="url(#photoTop)" role="img" aria-label="Uniformed chauffeur helping a business traveller with luggage into a black SUV"/>
        <path d="M0 262 H618 Q652 262 640 296 L522 610 H0 Z" fill="var(--red)"/>
        <path d="M632 262 Q656 264 648 296 L530 610 H545 L660 296 Q668 266 640 262 Z" fill="var(--black)"/>
        <path d="M0 712 H520 L474 830 Q464 855 438 855 H0 Z" fill="var(--black)"/>
        <path d="M545 620 H1130 V855 H565 L520 780 Z" fill="url(#photoBottom)" role="img" aria-label="Row of uniformed chauffeurs standing in front of the fleet"/>
        <path d="M555 838 H1130 V855 H565 Z" fill="var(--red)" opacity=".85"/>
        <path d="M0 1425 H520 Q538 1425 544 1442 L560 1495 H0 Z" fill="var(--black)"/>
        <path d="M0 1495 H560 L592 1585 H0 Z" fill="var(--red)"/>
        <path d="M548 1455 Q560 1450 566 1466 L598 1540 H1130 V1585 H608 L576 1500 Q568 1476 548 1455 Z" fill="var(--black)"/>
      </svg>

      <div class="brand">
        <span class="brand-dot"></span>
        <span class="brand-name">Quorvan Ride</span>
      </div>

      <h1 class="headline">Dallas to<br>Austin<br>Chauffeured<br>SUVs</h1>

      <p class="intro">Travel Dallas to Austin in a<br>new 2025 Norvak Tressel for</p>

      <div class="price">
        <span class="price-currency">$</span>
        <span class="price-amount">499</span>
        <span class="price-term">one<br>way</span>
      </div>

      <ul class="benefits benefits-left">
        <li>Trip includes a Uniformed<br>Chauffeur who has a Commercial<br>Drivers License (CDL)</li>
        <li>You can Schedule Chauffeur<br>Pickup at Your Home in Dallas</li>
        <li>Our Chauffeur will Drop You Off<br>at Your Final Destination in Austin</li>
        <li>You can Schedule Chauffeur<br>Return Pickup in Austin and<br>Return Back to Dallas.</li>
        <li>We offer Faster Times on Door-<br>to-Door Travel than Bluequill<br>Airways</li>
      </ul>

      <ul class="benefits benefits-right">
        <li>We offer Comparable Prices<br>on Door-to-Door Travel Times<br>than Bluequill Airways</li>
        <li>All of our trips are insured with $500k<br>of commercial auto insurance</li>
        <li>Our Passengers can Talk on Cell<br>Phone &amp; Conduct Kavlo calls<br>Throughout Travel</li>
        <li>Our Passengers have Maximum<br>Privacy, Comfort and First-Class<br>Amenities.</li>
        <li>Our Passengers Avoid Marrow Pike<br>Airfield and QHN Airport hassles &amp; delays</li>
        <li>Member Tellbrook Chamber of<br>Commerce, Pindle Chamber of<br>Commerce.</li>
      </ul>

      <div class="cta">
        <p class="cta-lead">Book your trip today at</p>
        <p class="cta-url">www.quorvanride.example</p>
      </div>
    </div>
  </div>
</div>
</body>
</html>
```